Local fast-growing company in the service sector

We are looking for a modern business card design, which should also appear on our letterheads

Target Market(s)

Private and industrial sectors

Contact Information for Business Card

Vorname Name
Kellberger Str. 18
74523 Steinbach
Tel.: 07146-839214-0
Name@agentur-kvtl.de

Colors
9d9d9d
919191
aaaaaa

Requirements
Must have
• The logo (file) in silver

```html
<!DOCTYPE html>
<html lang="de">
<head>
<meta charset="utf-8">
<title>KVTL Service – Visitenkarte</title>
<link rel="stylesheet" href="https://fonts.googleapis.com/css2?family=Open+Sans:wght@400;600;700&display=swap">
<style>
  :root {
    --stage: #2e2926;
    --card: #131313;
    --card-edge: #1c1c1c;
    --silver: #aaaaaa;
    --silver-mid: #9d9d9d;
    --silver-dark: #919191;
    --text-light: #e4e4e4;
  }
  * { margin: 0; padding: 0; box-sizing: border-box; }
  html, body {
    width: 1200px;
    height: 864px;
    overflow: hidden;
    background: var(--stage);
    font-family: "Open Sans", sans-serif;
  }
  .stage {
    position: relative;
    width: 1200px;
    height: 864px;
  }
  .card {
    position: absolute;
    width: 520px;
    height: 300px;
    background: var(--card);
    border: 1px solid var(--card-edge);
    box-shadow: 0 12px 30px rgba(0,0,0,0.45);
  }
  /* Front side */
  .card--front {
    left: 70px;
    top: 110px;
  }
  .brand {
    position: absolute;
    left: 120px;
    top: 92px;
    display: flex;
    align-items: center;
    gap: 18px;
  }
  .brand__mark {
    width: 54px;
    height: 54px;
    background: var(--silver);
  }
  .brand__name {
    font-weight: 700;
    font-size: 58px;
    letter-spacing: 2px;
    line-height: 1;
    color: var(--silver);
  }
  .brand__tagline {
    position: absolute;
    left: 194px;
    top: 160px;
    font-weight: 600;
    font-size: 18px;
    letter-spacing: 1px;
    color: var(--silver-dark);
  }
  .front__web {
    position: absolute;
    left: 0;
    right: 0;
    top: 226px;
    text-align: center;
    font-size: 16px;
    letter-spacing: 7px;
    color: var(--silver-dark);
  }
  /* Back side */
  .card--back {
    left: 610px;
    top: 440px;
  }
  .back__brand {
    position: absolute;
    left: 40px;
    top: 126px;
    display: flex;
    align-items: center;
    gap: 12px;
  }
  .back__brand .brand__mark {
    width: 30px;
    height: 30px;
  }
  .back__brand .brand__name {
    font-size: 34px;
  }
  .divider {
    position: absolute;
    left: 210px;
    top: 50px;
    width: 1px;
    height: 200px;
    background: linear-gradient(to bottom, transparent, var(--silver-mid), transparent);
  }
  .contact {
    position: absolute;
    left: 256px;
    top: 64px;
    list-style: none;
    color: var(--text-light);
    font-size: 17px;
    line-height: 26px;
  }
  .contact__name {
    font-weight: 700;
    font-size: 16px;
    color: var(--silver-mid);
    margin-bottom: 6px;
  }
  .contact__row {
    display: flex;
    align-items: center;
    gap: 8px;
  }
  .contact__row--icon {
    margin-left: -20px;
  }
  .contact__icon {
    width: 12px;
    height: 12px;
    flex: none;
    fill: var(--silver);
  }
</style>
</head>
<body>
<main class="stage">

  <section class="card card--front" aria-label="Visitenkarte Vorderseite">
    <div class="brand">
      <span class="brand__mark"></span>
      <span class="brand__name">KVTL</span>
    </div>
    <p class="brand__tagline">Service</p>
    <p class="front__web">www.agentur-kvtl.de</p>
  </section>

  <section class="card card--back" aria-label="Visitenkarte Rückseite">
    <div class="back__brand">
      <span class="brand__mark"></span>
      <span class="brand__name">KVTL</span>
    </div>
    <span class="divider"></span>
    <ul class="contact">
      <li class="contact__name">LENA HARTMANN</li>
      <li class="contact__row">Kellberger Str. 18</li>
      <li class="contact__row">74523 Steinbach</li>
      <li class="contact__row contact__row--icon">
        <svg class="contact__icon" viewBox="0 0 12 12" aria-hidden="true"><path d="M2.5 1 4.5 1 5.3 3.6 4 4.6C4.7 6 6 7.3 7.4 8L8.4 6.7 11 7.5 11 9.5C11 10.3 10.3 11 9.5 11 5 11 1 7 1 2.5 1 1.7 1.7 1 2.5 1Z"/></svg>
        07146-839214-0
      </li>
      <li class="contact__row contact__row--icon">
        <svg class="contact__icon" viewBox="0 0 12 12" aria-hidden="true"><path d="M1 2.5H11V9.5H1Z M1.6 3 6 6.5 10.4 3" fill="none" stroke="#aaaaaa" stroke-width="1.2"/></svg>
        Name@agentur-kvtl.de
      </li>
      <li class="contact__row contact__row--icon">
        <svg class="contact__icon" viewBox="0 0 12 12" aria-hidden="true"><circle cx="6" cy="6" r="5" fill="none" stroke="#aaaaaa" stroke-width="1.2"/><path d="M1 6H11M6 1C4 3.5 4 8.5 6 11M6 1C8 3.5 8 8.5 6 11" fill="none" stroke="#aaaaaa" stroke-width="1"/></svg>
        www.agentur-kvtl.de
      </li>
    </ul>
  </section>

</main>
</body>
</html>
```